Social Media App Needs PPT Template

We need a PowerPoint template for a new social media company based in the DC area called "Bold Ledger." We provide an interactive digital platform for executives to share actionable advice. We would like to see designs that use our orange logo color as an accent, but are mainly grey, white, and black. The final design should communicate clean, chic, modern, and professional.

Target Market(s)

Executives

Industry/Entity Type

Information Technology

Font styles to use
Sans Serif

Colors
f78f20
fbe7d2
ffffff
000000
e8e8e8
757575

Requirements
Must have
• My project must have title page and many options for the body of the ppt (graphs, tables, etc). It also needs to be easy to modify. I must have someone who is experienced in creating powerpoint templates.
Nice to have
• It would be nice to have a very modern and clean design that includes the logo on every page, but still leaves a lot of room for the content of the slide
Should not have
• My design project should not look to busy.

```html
<!DOCTYPE html>
<html lang="en">
<head>
<meta charset="utf-8">
<title>Bold Ledger – About Our Company</title>
<link rel="stylesheet" href="https://fonts.googleapis.com/css2?family=Lato:wght@300;400&display=swap">
<style>
  :root {
    --orange: #f78f20;
    --orange-deep: #e8821b;
    --orange-light: #f39a2c;
    --black: #000000;
    --white: #ffffff;
    --mat: #929292;
    --grey-bar: #6b6c6e;
    --ink: #555555;
    --grid: #9a9a9a;
  }
  html, body {
    margin: 0;
    padding: 0;
    width: 1200px;
    height: 960px;
    overflow: hidden;
    background: var(--mat);
    font-family: "Lato", sans-serif;
  }
  .page-label {
    position: absolute;
    left: 0;
    width: 1200px;
    top: 44px;
    text-align: center;
    font-weight: 300;
    font-size: 24px;
    color: #f4f4f4;
    margin: 0;
  }
  .slide {
    position: absolute;
    left: 68px;
    top: 106px;
    width: 1328px;
    height: 996px;
    transform: scale(0.8);
    transform-origin: 0 0;
    background: radial-gradient(ellipse at 50% 45%, #ffffff 0%, #f7f7f7 55%, #efefef 100%);
    overflow: hidden;
  }
  .slide-art {
    position: absolute;
    left: 0;
    top: 0;
  }
  .slide-title {
    position: absolute;
    left: 40px;
    top: 84px;
    margin: 0;
    font-weight: 300;
    font-size: 50px;
    color: var(--white);
    letter-spacing: 0.2px;
  }
  .brand {
    position: absolute;
    left: 1072px;
    top: 92px;
    display: flex;
    align-items: center;
    gap: 12px;
  }
  .brand-dot {
    width: 22px;
    height: 22px;
    border-radius: 50%;
    background: var(--orange);
  }
  .brand-name {
    font-weight: 400;
    font-size: 32px;
    color: var(--white);
    line-height: 1;
  }
  .body-copy {
    position: absolute;
    left: 67px;
    top: 722px;
    width: 1206px;
    margin: 0;
    font-size: 23.5px;
    line-height: 33.5px;
    text-align: justify;
    color: var(--ink);
  }
  .footer-text {
    position: absolute;
    left: 36px;
    top: 950px;
    margin: 0;
    font-size: 18px;
    color: var(--white);
  }
  .footer-text .sep { margin: 0 8px; }
  .axis-label { font-family: "Lato", sans-serif; font-size: 22px; fill: var(--ink); }
  .legend-label { font-family: "Lato", sans-serif; font-size: 26px; fill: var(--ink); }
</style>
</head>
<body>
  <p class="page-label">Page 6</p>

  <section class="slide">
    <svg class="slide-art" width="1328" height="996" viewBox="0 0 1328 996" xmlns="http://www.w3.org/2000/svg">
      <!-- header -->
      <polygon points="1032,44 1328,44 1328,57 1020,57" fill="var(--orange)"/>
      <polygon points="0,62 1010,62 905,167 0,167" fill="var(--orange-deep)"/>
      <polygon points="800,62 1010,62 950,122 720,145 " fill="var(--orange-light)" opacity="0.55"/>
      <polygon points="0,145 930,135 905,167 0,167" fill="var(--orange-light)" opacity="0.6"/>
      <polygon points="1020,62 1328,62 1328,167 907,167" fill="var(--black)"/>
      <polygon points="0,172 895,172 882,185 0,185" fill="var(--black)"/>

      <!-- chart grid -->
      <g stroke="var(--grid)" stroke-width="1.2" stroke-dasharray="10 8">
        <line x1="107" y1="290" x2="1098" y2="290"/>
        <line x1="107" y1="357" x2="1098" y2="357"/>
        <line x1="107" y1="424" x2="1098" y2="424"/>
        <line x1="107" y1="490" x2="1098" y2="490"/>
        <line x1="107" y1="557" x2="1098" y2="557"/>
      </g>
      <line x1="107" y1="286" x2="107" y2="624" stroke="var(--grid)" stroke-width="1.5"/>
      <line x1="100" y1="624" x2="1098" y2="624" stroke="var(--grid)" stroke-width="1.5"/>

      <g class="axis-label" text-anchor="end">
        <text x="86" y="302">5</text>
        <text x="86" y="369">4</text>
        <text x="86" y="434">3</text>
        <text x="86" y="501">2</text>
        <text x="86" y="567">1</text>
        <text x="86" y="636">0</text>
      </g>

      <!-- bars: value × 66.8 above baseline 624 -->
      <g>
        <rect x="163" y="337" width="65" height="287" fill="var(--orange)"/>
        <rect x="228" y="394" width="65" height="230" fill="var(--black)"/>
        <rect x="293" y="360" width="65" height="264" fill="var(--grey-bar)"/>

        <rect x="469" y="377" width="65" height="247" fill="var(--orange)"/>
        <rect x="534" y="333" width="65" height="291" fill="var(--black)"/>
        <rect x="599" y="397" width="65" height="227" fill="var(--grey-bar)"/>

        <rect x="764" y="414" width="65" height="210" fill="var(--orange)"/>
        <rect x="829" y="351" width="65" height="273" fill="var(--black)"/>
        <rect x="894" y="327" width="65" height="297" fill="var(--grey-bar)"/>
      </g>

      <g class="axis-label" text-anchor="middle">
        <text x="255" y="670">Category 1</text>
        <text x="561" y="670">Category 2</text>
        <text x="866" y="670">Category 3</text>
      </g>

      <!-- legend -->
      <rect x="1164" y="283" width="14" height="14" fill="var(--orange)"/>
      <rect x="1164" y="317" width="14" height="14" fill="var(--black)"/>
      <rect x="1164" y="354" width="14" height="14" fill="var(--grey-bar)"/>
      <text class="legend-label" x="1183" y="299">Series 1</text>
      <text class="legend-label" x="1183" y="333">Series 2</text>
      <text class="legend-label" x="1183" y="369">Series 3</text>

      <!-- footer -->
      <polygon points="0,943 380,943 340,982 0,982" fill="var(--black)"/>
      <polygon points="386,943 1328,943 1328,982 347,982" fill="var(--orange-deep)"/>
    </svg>

    <h1 class="slide-title">About Our Company</h1>

    <div class="brand">
      <span class="brand-dot"></span>
      <span class="brand-name">Bold Ledger</span>
    </div>

    <p class="body-copy">Duis autem vel eum iriure dolor in hendrerit in vulputate velit esse molestie consequat, vel illum dolore eu feugiat nulla facilisis at vero eros et accumsan et iusto odio dignissim qui blandit praesent luptatum zzril delenit augue duis dolore te feugait nulla facilisi. Nam liber tempor cum soluta nobis eleifend option congue nihil imperdiet doming id quod mazim placerat facer possim assum.</p>

    <p class="footer-text">www.boldledger.com<span class="sep">|</span>Page 4</p>
  </section>
</body>
</html>
```